Business Card Design Project

Business card based on attached logo

Todd Merrick
Todd@lorvantest.com
877-514-9073 ext. 318
Www.LorvanTest.com

Industry/Entity Type

Business

```html
<!DOCTYPE html>
<html lang="en">
<head>
<meta charset="utf-8">
<title>LorvanTest Business Card</title>
<link rel="stylesheet" href="https://fonts.googleapis.com/css2?family=Mulish:wght@400;700;800&display=swap">
<style>
  :root {
    --sheet-bg: #ece7e1;
    --card-white: #ffffff;
    --card-grey: #f1f1f1;
    --brand-red: #e3202b;
    --deep-red: #a81b20;
    --ink: #111111;
    --text-grey: #3a3a3a;
    --label: #2b2b2b;
  }
  * { margin: 0; padding: 0; box-sizing: border-box; }
  html, body { width: 1200px; height: 788px; overflow: hidden; }
  body {
    background: var(--sheet-bg);
    font-family: "Mulish", Arial, sans-serif;
    position: relative;
  }
  .view-label {
    position: absolute;
    width: 525px;
    text-align: center;
    font-size: 21px;
    color: var(--label);
  }
  .card {
    position: absolute;
    width: 525px;
    height: 300px;
    border-radius: 20px;
    overflow: hidden;
    background: var(--card-white);
    box-shadow: 0 4px 12px rgba(0,0,0,.18);
  }
  .card--front { left: 54px; top: 74px; }
  .card--back-white { left: 622px; top: 74px; }
  .card--back-red { left: 54px; top: 445px;
    background: linear-gradient(180deg, var(--brand-red) 0%, var(--deep-red) 100%); }
  .card--back-grey { left: 622px; top: 445px;
    background: linear-gradient(180deg, #fafafa 0%, #e6e6e6 100%); }

  .wordmark {
    position: absolute;
    display: flex;
    align-items: center;
    gap: 12px;
    font-weight: 800;
    color: var(--ink);
    white-space: nowrap;
    letter-spacing: -0.5px;
  }
  .wordmark__square { background: var(--brand-red); flex: none; }
  .card--back-red .wordmark__square { background: #ffffff; }

  .contact-name {
    position: absolute; left: 310px; top: 88px;
    color: var(--brand-red); font-weight: 700; font-size: 17px;
  }
  .contact-phone {
    position: absolute; left: 308px; top: 116px;
    font-size: 13.5px; color: var(--text-grey);
    display: flex; align-items: center; gap: 4px;
  }
  .front-bands { position: absolute; left: 0; top: 0; }
  .band-text {
    position: absolute; color: #fff; font-size: 13px;
  }
  .band-text--web { left: 36px; top: 234px; }
  .band-text--mail { left: 310px; top: 254px; }

  .back-url {
    position: absolute; left: 0; width: 100%; bottom: 28px;
    text-align: center; font-size: 18px; color: var(--text-grey);
  }
  .card--back-red .back-url { color: #ffffff; }

  .raised-panel {
    position: absolute; left: 81px; top: 82px; width: 362px; height: 130px;
    background: linear-gradient(180deg, #ffffff, #f4f4f4);
    border: 1px solid #dcdcdc;
    box-shadow: 0 8px 10px -6px rgba(0,0,0,.35);
  }
</style>
</head>
<body>
  <div class="view-label" style="left:54px;top:34px;">Front</div>
  <div class="view-label" style="left:622px;top:34px;">Back - 1</div>
  <div class="view-label" style="left:54px;top:404px;">Back - 2</div>
  <div class="view-label" style="left:622px;top:404px;">Back - 3</div>

  <section class="card card--front">
    <div class="wordmark" style="left:36px;top:100px;font-size:44px;">
      LorvanTest<span class="wordmark__square" style="width:20px;height:20px;"></span>
    </div>
    <div class="contact-name">Todd Merrick</div>
    <div class="contact-phone">
      <svg width="11" height="11" viewBox="0 0 24 24" aria-hidden="true"><path fill="#e3202b" d="M6.6 10.8a15 15 0 0 0 6.6 6.6l2.2-2.2c.3-.3.7-.4 1-.2 1.1.4 2.3.6 3.6.6.6 0 1 .4 1 1V20c0 .6-.4 1-1 1A17 17 0 0 1 3 4c0-.6.4-1 1-1h3.5c.6 0 1 .4 1 1 0 1.3.2 2.5.6 3.6.1.3 0 .7-.2 1z"/></svg>
      877-514-9073 ext. 318
    </div>
    <svg class="front-bands" width="525" height="300" aria-hidden="true">
      <polygon points="242,244 525,244 525,278 242,278 274,244" fill="#8a1015" opacity=".35"/>
      <polygon points="0,225 307,225 278,262 0,262" fill="#0d0d0d"/>
      <polygon points="272,244 525,244 525,278 242,278" fill="#e3202b"/>
    </svg>
    <div class="band-text band-text--web">www.LorvanTest.com</div>
    <div class="band-text band-text--mail">Todd@lorvantest.com</div>
  </section>

  <section class="card card--back-white">
    <div class="wordmark" style="left:138px;top:92px;font-size:46px;">
      LorvanTest<span class="wordmark__square" style="width:22px;height:22px;"></span>
    </div>
    <div class="back-url">www.LorvanTest.com</div>
  </section>

  <section class="card card--back-red">
    <div class="wordmark" style="left:138px;top:92px;font-size:46px;">
      LorvanTest<span class="wordmark__square" style="width:22px;height:22px;"></span>
    </div>
    <div class="back-url">www.LorvanTest.com</div>
  </section>

  <section class="card card--back-grey">
    <div class="raised-panel"></div>
    <div class="wordmark" style="left:176px;top:124px;font-size:36px;">
      LorvanTest<span class="wordmark__square" style="width:17px;height:17px;"></span>
    </div>
    <div class="back-url">www.LorvanTest.com</div>
  </section>
</body>
</html>
```